"LuvaWorks" Graphic Design Project

We are a new business creating bath/ body/beauty products. We need label designs for men "Velto for Men " and women- "Velto for Women" . Since the collection called Velto will be used for both- we'd like the labels to look similar but separating the gender look- maybe by a same color variation. Our bottles are amber in color , so we like the beiges, cream, and earthy warm tones - greens- brown-orange- yellow-colors. The labels are for 8 oz amber cosmo round bottles. The height is 7.32inches and the diameter is 1.85 inches.
Our starting line will be Velto for Men ( Silk Body Wash, Silk Body Lotion and Body Mist) and the same for Velto for Women.

Target Market(s)

Our target audience is between 30 to 60 years of age. Salons and private consumers.
I am including attached sample of what was started by me.

Requirements
Must have
• We would like to incorporate the company name- LuvaWorks along with the name of the product- which will be Velto for Men or Velto for Women on each label.

On label with company name or somewhere on label we would like a tree to symbolize the beginning, but we are open to suggestions.

```html
<!DOCTYPE html>
<html lang="en">
<head>
<meta charset="utf-8">
<title>Velto for Men – Silk Body Wash Label</title>
<link href="https://fonts.googleapis.com/css2?family=Jost:wght@300;400&display=swap" rel="stylesheet">
<style>
  :root {
    --olive-top: #8a9852;
    --olive-mid: #66703a;
    --earth-brown: #4e3d24;
    --bark-dark: #2a1e14;
    --spine-core: #4a4426;
    --spine-edge: #302a16;
    --cream: #fbf3e2;
    --cream-soft: #f3e9d2;
    --honey: #e0b65a;
    --panel-fill: rgba(255, 240, 210, 0.15);
    --bubble-fill: rgba(245, 215, 150, 0.2);
    --emblem-fill: #c98f3c;
  }
  html, body { margin: 0; padding: 0; overflow: hidden; background: #ffffff; }
  .label {
    position: relative;
    width: 955px;
    height: 1200px;
    overflow: hidden;
    font-family: "Jost", "Helvetica Neue", Arial, sans-serif;
    font-weight: 300;
    color: var(--cream);
    background: linear-gradient(180deg, var(--olive-top) 0%, var(--olive-mid) 42%, var(--earth-brown) 72%, var(--bark-dark) 100%);
  }
  .bubble-field { position: absolute; inset: 0; }
  .spine {
    position: absolute;
    left: 325px; top: 0;
    width: 97px; height: 1200px;
    background: linear-gradient(90deg, var(--spine-edge) 0%, var(--spine-core) 18%, var(--spine-core) 82%, var(--spine-edge) 100%);
    opacity: 0.92;
  }
  .spine-brand {
    position: absolute;
    left: 373px; top: 600px;
    transform: translate(-50%, -50%) rotate(-90deg);
    font-size: 76px;
    font-weight: 300;
    white-space: nowrap;
    color: var(--cream);
  }
  .tree-emblem { position: absolute; left: 359px; top: 388px; }
  .front { position: absolute; left: 0; top: 0; width: 325px; height: 1200px; text-align: center; }
  .front div { position: absolute; left: 0; width: 325px; white-space: nowrap; }
  .product-name {
    top: 136px;
    font-size: 80px; line-height: 1; font-weight: 300;
    color: var(--honey);
    opacity: 0.85;
  }
  .audience { top: 222px; padding-left: 84px; box-sizing: border-box; font-size: 25px; font-weight: 400; }
  .variant { top: 612px; font-size: 32px; font-weight: 400; }
  .volume { top: 1110px; padding-left: 16px; box-sizing: border-box; font-size: 22px; line-height: 34px; font-weight: 400; }
  .back { position: absolute; left: 450px; width: 500px; top: 0; text-align: center; }
  .back p {
    margin: 0; position: absolute; left: 0; width: 500px;
    font-size: 24px; line-height: 33px; white-space: nowrap; color: var(--cream-soft);
  }
  .intro { top: 94px; }
  .directions { top: 224px; }
  .warnings { top: 320px; }
  .claim { top: 421px; }
  .ingredients {
    position: absolute; left: 442px; top: 554px;
    width: 484px; height: 418px;
    box-sizing: border-box;
    padding: 36px 6px 0;
    border-radius: 14px;
    background: var(--panel-fill);
    font-size: 18px; line-height: 25px;
    white-space: nowrap;
    text-align: center; color: var(--cream-soft);
  }
  .maker {
    position: absolute; left: 450px; width: 500px; top: 1056px;
    text-align: center; font-size: 24px; line-height: 33px; color: var(--cream-soft);
  }
</style>
</head>
<body>
<main class="label">
  <svg class="bubble-field" width="955" height="1200" viewBox="0 0 955 1200" role="img" aria-label="Soft bubble decoration scattered across a warm olive background">
    <circle cx="150" cy="280" r="62" fill="var(--bubble-fill)"/>
    <circle cx="305" cy="310" r="22" fill="var(--bubble-fill)"/>
    <circle cx="790" cy="175" r="75" fill="var(--bubble-fill)"/>
    <circle cx="640" cy="455" r="90" fill="var(--bubble-fill)" opacity="0.7"/>
    <circle cx="860" cy="250" r="55" fill="var(--bubble-fill)" opacity="0.8"/>
    <circle cx="250" cy="700" r="70" fill="var(--bubble-fill)" opacity="0.5"/>
    <circle cx="780" cy="560" r="28" fill="var(--bubble-fill)" opacity="0.7"/>
  </svg>

  <div class="spine"></div>
  <svg class="tree-emblem" width="28" height="28" viewBox="0 0 28 28" role="img" aria-label="Place for the tree emblem symbolising a new beginning">
    <circle cx="14" cy="14" r="13" fill="var(--emblem-fill)"/>
  </svg>
  <div class="spine-brand">LuvaWorks</div>

  <section class="front">
    <div class="product-name">Velto</div>
    <div class="audience">FOR MEN</div>
    <div class="variant">Silk Body Wash</div>
    <div class="volume">MADE IN USA<br>8.25 fl oz. / 244mL</div>
  </section>

  <section class="back">
    <p class="intro">Our Nourishing Silk Body Wash will engulf you<br>in luxurious lather as it gently cleanses your<br>delicate skin leaving it soft as silk.</p>
    <p class="directions">Directions: Apply to skin while damp with<br>sponge or wash cloth. Rinse well.</p>
    <p class="warnings">WARNINGS/CAUTIONS: For external use only.<br>Avoid contact with eyes.</p>
    <p class="claim">NOT TESTED ON ANIMALS</p>
  </section>

  <div class="ingredients">INGREDIENTS: purified water, sodium olefin<br>sulfonate (plant source), organic aloe barbadensis<br>leaf juice, cocamidopropyl betaine (plant source),<br>sodium chloride (salt), kosher vegetable glycerin,<br>tocopherol (natural vitamin E), polysorbate 20<br>(plant source), potassium sorbate (plant source),<br>phenoxyethanol (mild preservative), caprylyl glycol<br>(plant source), organic anthemis nobilis (chamo-<br>mile) extract, organic calendula officinalis flower<br>extract, xanthan gum (plant source), magnesium<br>ascorbyl phosphate (vitamin C ester), sodium<br>bicarbonate (baking soda), citric acid fragrance.</div>

  <div class="maker">LuvaWorks<br>Bath – Body - Home<br>Coral Bay, FL&nbsp; 33250<br>Shop 24/7 - www.luvaworks.com</div>
</main>
</body>
</html>
```